PowerPoint Listing Presentation for Real Estate Agency

We need a PowerPoint presentation for a new real estate brokerage team.

[[[[[[submit 1-3 sample slides for review - i will provide feedback and you can make changes if you want to - we will not be deciding on a design prior to the deadline]]]]]

******ATTN: DESIGNERS, if your skills are webdesign then just look at this like a portable website or a brochure. it should be easy enough******

NOTE: we have all the data to put into the slides. You just need to come up with the design and layout. we have a sample design that we like and have provided.

This focus will be for the home listing side of the business (a presentation for home sellers to convince them to use our services). The data and slides will present our team and the benefits, in the best light, to use our services over that of other real estate agent applying for the job. This presentation will proved facts and benefits and describe our special and unique offerings that will show a home seller why we can sell their home for more money in less time and with the least amount of hassle. The main color scheme is Dark Blue and White (we want some additional colors included - based on your creativity. otherwise the presentation will too monotone). We would like to see the use of Statistical Graphs (3-D) - data provided. We have photos of our team and a new logo (the logo could have some minor adjustment to clean it up if necessary) - also uploaded. We have about 80-90% of the information that will be put into the slides and will need to work closely to get the design and data integrated into the presentation (should be easier then it sounds). We should be able to add slides and data 'at will' over time via our master slides built into the presentation. We have a pretty good sample presentation that we like and can be used as a guideline (this is from our affiliated business network and we have full rights to all the information), it is uploaded but doesn't contain all the slide because of size limitations.

NOTE: An additional buyers presentation will be needed after we get the sellers presentation completed, which means additional work.

This should be enough to get you started and we are available if you have any questions to help you with the project. there will be around 60-70 total slides. once concept is completed it will be easy to create the slides.

Target Market(s)

home sellers. people who are moving to a new and better home or relocation for job reasons. typically more established in life

Industry/Entity Type

Real Estate

Requirements
Must have
• all the slides must be congruent. in other words, the exact same layout feel should used across the board. we are working on building our trade dress/image. Also, it must have a soft and inviting overall feel, yet show strength of ability.
Nice to have
• nice to have use of real people images when necessary. 3D graphs would be nice. clean modern look and feel, yet sophisticated and professional.
Should not have
• should not have a lot of time consuming transitions. do not include 3D stick figures or distracting moving gifs

```html
<!DOCTYPE html>
<html lang="en">
<head>
<meta charset="utf-8">
<title>Why Marlowe &amp; Reed?</title>
<link rel="stylesheet" href="https://fonts.googleapis.com/css2?family=Ubuntu:wght@500;700&display=swap">
<style>
  :root {
    --navy: #1b2136;
    --frame-dark: #6f7072;
    --frame-mid: #8c8d8f;
    --panel-light: #a9aaac;
    --panel-mid: #97989a;
    --edge: #5d5e60;
  }
  html, body {
    margin: 0;
    padding: 0;
    overflow: hidden;
    background: var(--frame-mid);
  }
  .slide {
    position: relative;
    width: 1200px;
    height: 675px;
    overflow: hidden;
    background: linear-gradient(180deg, var(--frame-mid), var(--frame-dark));
    font-family: "Ubuntu", "Trebuchet MS", sans-serif;
    color: var(--navy);
  }
  .title-bar {
    position: absolute;
    left: 14px;
    top: 14px;
    width: 1172px;
    height: 76px;
    box-sizing: border-box;
    border: 2px solid var(--edge);
    background: linear-gradient(180deg, var(--panel-light), var(--panel-mid));
    display: flex;
    align-items: center;
    padding-left: 20px;
  }
  .title {
    margin: 0;
    font-size: 44px;
    font-weight: 700;
    letter-spacing: 0.5px;
    text-shadow: 2px 2px 2px rgba(255, 255, 255, 0.45);
  }
  .content-panel {
    position: absolute;
    left: 14px;
    top: 104px;
    width: 1172px;
    height: 538px;
    box-sizing: border-box;
    border: 2px solid var(--edge);
    background: radial-gradient(ellipse at 40% 40%, var(--panel-light), var(--panel-mid) 80%);
  }
  .benefits {
    list-style: none;
    margin: 0;
    padding: 0;
    position: absolute;
    left: 28px;
    top: 96px;
  }
  .benefit {
    display: flex;
    align-items: center;
    height: 66px;
    margin-bottom: 42px;
    font-size: 37px;
    font-weight: 700;
    letter-spacing: 0.6px;
  }
  .benefit-marker {
    width: 34px;
    height: 34px;
    background: var(--navy);
    margin-right: 22px;
    flex: none;
  }
  .brand-mark {
    position: absolute;
    right: 14px;
    bottom: 20px;
    font-size: 30px;
    font-weight: 700;
    color: var(--navy);
  }
</style>
</head>
<body>
  <main class="slide">
    <header class="title-bar">
      <h1 class="title">Why MARLOWE &amp; REED ?</h1>
    </header>
    <section class="content-panel">
      <ul class="benefits">
        <li class="benefit"><span class="benefit-marker"></span>Simple, Fast &amp; Hassle Free Transaction at Best Price</li>
        <li class="benefit"><span class="benefit-marker"></span>Amazing Success Rate of 98%</li>
        <li class="benefit"><span class="benefit-marker"></span>Guaranteed Sale &amp; Trade Up Program</li>
      </ul>
      <div class="brand-mark">MARLOWE &amp; REED</div>
    </section>
  </main>
</body>
</html>
```